Box Design for Flooring product

***IMPORTANT: PLEASE READ THE DOCUMENT PROVIDED WITH THIS BRIEF CAREFULLY BEFORE ACCEPTING THIS PROJECT***
Need a creative design for the packaging of a flooring product. The packaging is two boxes: one holding 36 planks of flooring, and the other 7 planks of flooring. There are 4 colours for the flooring planks that need a box designed (for both the 36 plank box and 7 plank box). The boxes measures 92 cm x 16cm x 7cm (36 planks) and 92 cm x 16cm x 1.5cm (7 planks).
More details are provided in the requirements document attached with this brief. Also attaching other supporting documents with this brief mentioned in the document.
Updates
Font styles to use
Other font styles liked:
- Montserrat-Regular
Look and feel
Each slider illustrates characteristics of the customer's brand and the style your logo design should communicate.

```html
<!DOCTYPE html>
<html lang="en">
<head>
<meta charset="utf-8">
<title>Terralune – Self Adhesive Vinyl Planks – 36 Plank Box Dieline</title>
<link href="https://fonts.googleapis.com/css2?family=Montserrat:wght@400;500;600;700&display=swap" rel="stylesheet">
<style>
  :root{
    --olive:#4b4a39;
    --brown:#372519;
    --paper:#ffffff;
    --ink:#1e1e1e;
    --thumb:#b9b3a0;
    --photo-a:#24413f;
    --photo-b:#4a3222;
  }
  html,body{margin:0;padding:0;width:1200px;height:1000px;overflow:hidden;background:var(--paper);}
  .dieline{position:absolute;left:20px;top:205px;width:1160px;height:589px;display:block;}
  .dieline text{font-family:'Montserrat',sans-serif;}
  .olive{fill:var(--olive);}
  .brown{fill:var(--brown);}
  .cut{fill:var(--paper);}
  .brand{fill:var(--paper);font-weight:500;letter-spacing:1px;}
  .headline{fill:var(--paper);font-weight:700;}
  .sub{fill:var(--paper);font-weight:400;}
  .panel-white{fill:var(--paper);}
  .dark-text{fill:var(--ink);}
  .tiny{font-size:4px;fill:#444;}
  .tiny-title{font-size:4.2px;font-weight:600;fill:#222;}
  .thumb{fill:var(--thumb);}
</style>
</head>
<body>
<svg class="dieline" viewBox="80 55 1260 640" xmlns="http://www.w3.org/2000/svg">
  <defs>
    <linearGradient id="roomGrad" x1="0" y1="0" x2="0" y2="1">
      <stop offset="0" stop-color="var(--photo-a)"/>
      <stop offset="0.55" stop-color="#2f3f35"/>
      <stop offset="1" stop-color="var(--photo-b)"/>
    </linearGradient>
    <clipPath id="boxBody">
      <polygon points="190,62 1250,62 1275,145 1335,145 1335,688 85,688 85,145 165,145"/>
    </clipPath>
  </defs>

  <!-- body colour fields -->
  <g class="fields" clip-path="url(#boxBody)">
    <rect class="olive" x="80" y="55" width="1260" height="640"/>
    <polygon class="brown" points="1000,55 1340,55 1340,695 768,695"/>
    <polygon class="olive" points="1022,55 1040,55 808,695 790,695"/>
    <polygon class="olive" points="1052,55 1062,55 830,695 820,695"/>
    <polygon class="olive" points="915,603 975,603 975,695 880,695"/>
  </g>

  <!-- fold / cut gaps -->
  <g class="gaps">
    <rect class="cut" x="80" y="333" width="1260" height="7"/>
    <rect class="cut" x="80" y="410" width="1260" height="8"/>
    <rect class="cut" x="80" y="603" width="1260" height="7"/>
    <rect class="cut" x="160" y="418" width="4" height="185"/>
    <rect class="cut" x="1250" y="418" width="4" height="185"/>
    <rect class="cut" x="80" y="142" width="1260" height="3"/>
  </g>

  <!-- lid panel -->
  <g class="lid-panel">
    <text class="brand" x="190" y="192" font-size="26">TERRALUNE</text>
    <text class="headline" x="190" y="267" font-size="24">SELF ADHESIVE</text>
    <text class="headline" x="190" y="293" font-size="24">VINYL PLANKS</text>
    <text class="sub" x="190" y="312" font-size="12">Suitable for general domestic use</text>

    <g class="instructions">
      <rect class="panel-white" x="472" y="156" width="393" height="165" rx="5"/>
      <text class="tiny-title" x="479" y="165" font-size="5">Installation instructions</text>
      <g>
        <text class="tiny-title" x="479" y="172">Step 1 : Tools needed</text>
        <rect class="thumb" x="479" y="175" width="22" height="20"/>
        <text class="tiny" x="505" y="180">Knife, ruler, pencil and cloth.</text>
        <text class="tiny-title" x="479" y="205">Step 2 : Acclimatise your floor</text>
        <rect class="thumb" x="479" y="208" width="22" height="20"/>
        <text class="tiny" x="505" y="213">Leave planks in room for 48 hours.</text>
        <text class="tiny-title" x="479" y="257">Step 3 : Removing skirting board</text>
        <rect class="thumb" x="479" y="260" width="22" height="20"/>
        <text class="tiny" x="505" y="265">Remove skirting boards if needed.</text>
        <text class="tiny-title" x="479" y="290">Step 4 : Planning your layout</text>
        <rect class="thumb" x="479" y="293" width="22" height="20"/>
        <text class="tiny" x="505" y="298">Start from the longest straight wall.</text>
      </g>
      <g>
        <text class="tiny-title" x="608" y="172">Step 5 : Get ready to lay</text>
        <rect class="thumb" x="608" y="175" width="22" height="20"/>
        <text class="tiny" x="634" y="180">Sweep floor clean, dry and level.</text>
        <text class="tiny-title" x="608" y="205">Step 6 : Dry lay your planks</text>
        <rect class="thumb" x="608" y="208" width="22" height="20"/>
        <text class="tiny" x="634" y="213">Mix planks from several boxes.</text>
        <text class="tiny-title" x="608" y="257">Step 7 : Arrows on backing paper</text>
        <rect class="thumb" x="608" y="260" width="22" height="20"/>
        <text class="tiny" x="634" y="265">Keep arrows facing one direction.</text>
        <text class="tiny-title" x="608" y="290">Step 8 : Laying the first plank</text>
        <rect class="thumb" x="608" y="293" width="22" height="20"/>
        <text class="tiny" x="634" y="298">Peel backing, press firmly down.</text>
      </g>
      <g>
        <text class="tiny-title" x="738" y="172">Step 9 : Laying remaining planks</text>
        <rect class="thumb" x="738" y="175" width="22" height="20"/>
        <text class="tiny" x="764" y="180">Stagger joints row by row.</text>
        <text class="tiny-title" x="738" y="205">Step 10 : Cutting the planks</text>
        <rect class="thumb" x="738" y="208" width="22" height="20"/>
        <text class="tiny" x="764" y="213">Score the top surface with knife.</text>
        <text class="tiny-title" x="738" y="257">Step 11 : Breaking the cut plank</text>
        <rect class="thumb" x="738" y="260" width="22" height="20"/>
        <text class="tiny" x="764" y="265">Snap along the scored line.</text>
        <text class="tiny-title" x="738" y="290">Step 12 : Laying the cut planks</text>
        <rect class="thumb" x="738" y="293" width="22" height="20"/>
        <text class="tiny" x="764" y="298">Fit cut planks at the row ends.</text>
      </g>
    </g>

    <g class="producer" font-size="7" fill="#fff" text-anchor="end">
      <text x="1108" y="167" font-weight="600">Produced by :</text>
      <text x="1108" y="176">Terralune</text>
      <text x="1108" y="184">Sample address, Unit #</text>
      <text x="1108" y="192">City, 12345</text>
      <text x="1108" y="200">www.terralune-floors.example</text>
      <text x="1108" y="208" font-weight="600">Costumer Service :</text>
      <text x="1108" y="216">123-456-7890</text>
    </g>

    <g class="cert-table">
      <rect class="panel-white" x="1003" y="228" width="105" height="87"/>
      <rect x="1035" y="233" width="40" height="26" fill="#1e1e1e"/>
      <line x1="1003" y1="263" x2="1108" y2="263" stroke="#1e1e1e" stroke-width="0.8"/>
      <text class="dark-text" x="1055" y="270" font-size="5" text-anchor="middle">Terralune™</text>
      <text class="dark-text" x="1055" y="276" font-size="4.5" text-anchor="middle">Premium Floors and Tiles</text>
      <line x1="1003" y1="279" x2="1108" y2="279" stroke="#1e1e1e" stroke-width="0.5"/>
      <text class="dark-text" x="1006" y="285" font-size="4.2">EN 14041, EN 13501-1, EN 717-1, EN 13893</text>
      <line x1="1003" y1="288" x2="1108" y2="288" stroke="#1e1e1e" stroke-width="0.5"/>
      <text class="dark-text" x="1006" y="294" font-size="4.5" font-weight="600">Reaction to Fire</text>
      <text class="dark-text" x="1104" y="294" font-size="4.5" text-anchor="end">Bfl-S1</text>
      <line x1="1003" y1="297" x2="1108" y2="297" stroke="#1e1e1e" stroke-width="0.5"/>
      <text class="dark-text" x="1006" y="303" font-size="4.5" font-weight="600">Emission of Formaldehyde</text>
      <text class="dark-text" x="1104" y="303" font-size="4.5" text-anchor="end">E1</text>
      <line x1="1003" y1="306" x2="1108" y2="306" stroke="#1e1e1e" stroke-width="0.5"/>
      <text class="dark-text" x="1006" y="312" font-size="4.5" font-weight="600">Slipperiness</text>
      <text class="dark-text" x="1104" y="312" font-size="4.5" text-anchor="end">DS</text>
    </g>

    <g class="pack-label">
      <rect class="panel-white" x="1118" y="161" width="134" height="30"/>
      <text class="dark-text" x="1192" y="188" font-size="26" font-weight="700" text-anchor="end">36</text>
      <text class="dark-text" x="1196" y="188" font-size="11" font-weight="600">Planks</text>
      <text x="1118" y="205" font-size="11" font-weight="600" fill="#fff">Pack coverage 5 m²</text>
      <rect x="1124" y="210" width="102" height="43" fill="none" stroke="#fff" stroke-width="1"/>
      <text x="1222" y="221" font-size="8" fill="#fff" text-anchor="end">Plank Size :</text>
      <text x="1222" y="231" font-size="8" fill="#fff" text-anchor="end">914 mm x 152 mm</text>
      <text x="1222" y="239" font-size="6" fill="#fff" text-anchor="end">(36" x 6" approx.)</text>
      <text x="1222" y="249" font-size="8" fill="#fff" text-anchor="end">1.8 mm (0.07") Thickness</text>
    </g>
  </g>

  <!-- inverted strip -->
  <g class="inverted-strip">
    <text class="headline" transform="translate(697,363) rotate(180)" font-size="30">SELF ADHESIVE VINYL PLANKS</text>
    <text class="brand" transform="translate(1228,360) rotate(180)" font-size="26">TERRALUNE</text>
  </g>

  <!-- front panel -->
  <g class="front-panel">
    <text class="brand" transform="translate(128,452) rotate(90)" font-size="13">TERRALUNE</text>

    <text class="brand" x="190" y="463" font-size="26">TERRALUNE</text>
    <text class="headline" x="190" y="559" font-size="30">SELF ADHESIVE VINYL PLANKS</text>
    <text class="sub" x="190" y="583" font-size="14">Suitable for general domestic use</text>

    <g class="feature-icons" font-size="5.5" fill="#fff" text-anchor="middle">
      <rect x="592" y="433" width="52" height="52" rx="4" fill="#c9c4ad" role="img" aria-label="Icon: plank being laid"/>
      <text x="618" y="493">Easy to lay</text>
      <rect x="655" y="433" width="52" height="52" rx="4" fill="#3fb6c4" role="img" aria-label="Icon: water and cleaning brush"/>
      <text x="681" y="493">Water resistant,</text>
      <text x="681" y="499">easy to clean</text>
      <rect x="718" y="433" width="52" height="52" rx="4" fill="#e7cf72" role="img" aria-label="Icon: bathroom and kitchen"/>
      <text x="744" y="493">Ideal for Bathrooms</text>
      <text x="744" y="499">and Kitchens</text>
    </g>

    <rect x="860" y="418" width="390" height="185" fill="url(#roomGrad)" role="img" aria-label="Living room with green sofa on dark brown plank floor"/>
    <polygon points="860,418 915,418 860,560" class="brown" opacity="0"/>
    <polygon points="803,585 858,478 913,585" fill="#fff"/>

    <g class="front-label">
      <rect class="panel-white" x="1068" y="434" width="186" height="28"/>
      <text class="dark-text" x="1170" y="460" font-size="26" font-weight="700" text-anchor="end">36</text>
      <text class="dark-text" x="1174" y="460" font-size="13" font-weight="600">Planks</text>
      <rect class="brown" x="1068" y="462" width="186" height="30"/>
      <text x="1074" y="482" font-size="14" font-weight="600" fill="#fff">Pack coverage 5 m²</text>
      <rect class="brown" x="1068" y="492" width="160" height="54"/>
      <rect x="1068" y="492" width="160" height="54" fill="none" stroke="#fff" stroke-width="1"/>
      <text x="1222" y="505" font-size="11" fill="#fff" text-anchor="end">Plank Size :</text>
      <text x="1222" y="517" font-size="11" fill="#fff" text-anchor="end">914 mm x 152 mm</text>
      <text x="1222" y="527" font-size="8" fill="#fff" text-anchor="end">(36" x 6" approx.)</text>
      <text x="1222" y="540" font-size="11" fill="#fff" text-anchor="end">1.8 mm (0.07") Thickness</text>
      <rect x="1040" y="555" width="197" height="37" rx="6" fill="#fff"/>
      <rect x="1044" y="559" width="189" height="29" rx="4" fill="#5a3a26"/>
      <text x="1048" y="582" font-size="13" fill="#fff">DARK BROWN</text>
    </g>

    <g class="side-flap" fill="#fff">
      <text transform="translate(1296,558) rotate(-90)" font-size="22" font-weight="700">36 <tspan font-size="14" font-weight="600">Planks</tspan></text>
      <text transform="translate(1314,566) rotate(-90)" font-size="13">DARK BROWN</text>
    </g>
  </g>

  <!-- base strip -->
  <g class="base-strip">
    <text class="brand" x="190" y="655" font-size="26">TERRALUNE</text>
    <text x="810" y="648" font-size="26" font-weight="700" fill="#fff">36 <tspan font-size="14" font-weight="600">Planks</tspan></text>
    <text x="802" y="666" font-size="14" fill="#fff">DARK BROWN</text>
  </g>
</svg>
</body>
</html>
```